Wine Label Redesign For California Wine Company

We’re looking to refresh our brand with a new professional looking label. We love what we have and was well received over the past three years and would like to keep a couple of the element: Name (Mark Dunlow), it doesn’t have to be in cursive. The swirl, this how everybody recognizes our brand as it’s also in our logo. Colors: Gold and whatever you think is awesome. Looking forward to seeing your work.

Target Market(s)

Retailers

Industry/Entity Type

Winery

Font styles to use
Serif
Script

Colors

Designer to choose colors to be used in the design.

Requirements
Must have
• Front Label:
• Symphony (Varietal)
• 2016 (vintage)
• Lodi, California (location)
• Mark Dunlow (Name)
• Back Label:
• Government Warning
• www.dunlowvinco.com (website)
• 2016 (vintage)
• Swirl
Nice to have
• Creativity
• Bold colors
• Something that pops
Should not have
• Should not look nothing like my old label.

```html
<!DOCTYPE html>
<html lang="en">
<head>
<meta charset="utf-8">
<title>Symphony – Mark Dunlow Wine Labels</title>
<link href="https://fonts.googleapis.com/css2?family=Cinzel:wght@400;700;900&family=Cormorant+Garamond:wght@700&display=swap" rel="stylesheet">
<style>
  :root {
    --backdrop: #b6aea8;
    --label-black: #050505;
    --gold: #d8b04a;
    --cream-light: #fbf7ee;
    --cream: #e9dfcb;
    --cream-deep: #d9ccb2;
    --ink: #0d0d0d;
    --warning-ink: #1e1a14;
    --year: #e9e4d8;
  }
  * { margin: 0; padding: 0; box-sizing: border-box; }
  html, body { width: 874px; height: 1200px; overflow: hidden; }
  body {
    background: var(--backdrop);
    position: relative;
    font-family: "Cinzel", serif;
  }
  .label {
    position: absolute;
    top: 420px;
    width: 304px;
    height: 360px;
    background: var(--label-black);
    display: flex;
    flex-direction: column;
  }
  .label--front { left: 110px; }
  .label--back { left: 456px; width: 308px; }

  .label__top {
    height: 53px;
    display: flex;
    align-items: center;
    justify-content: center;
    border-bottom: 2px solid var(--gold);
    margin-bottom: 3px;
  }
  .varietal {
    color: var(--gold);
    font-size: 24px;
    letter-spacing: 9px;
    font-weight: 400;
    padding-left: 9px;
  }
  .website {
    color: var(--gold);
    font-size: 14px;
    font-weight: 700;
    letter-spacing: 0.3px;
  }

  .label__panel {
    position: relative;
    height: 230px;
    overflow: hidden;
    background:
      linear-gradient(90deg, rgba(217,204,178,0.9) 0%, rgba(251,247,238,0) 30%, rgba(251,247,238,0) 70%, rgba(217,204,178,0.9) 100%),
      linear-gradient(180deg, var(--cream) 0%, var(--cream-light) 30%, var(--cream-light) 60%, var(--cream) 100%);
  }

  .brand-mark {
    position: absolute;
    left: 66px;
    top: 60px;
    width: 108px;
    height: 108px;
    border-radius: 50%;
    background: radial-gradient(circle at 40% 35%, #e9d36a 0%, #c8ad3d 55%, #8e7c3a 100%);
  }
  .producer {
    position: absolute;
    left: 178px;
    top: 66px;
    color: var(--ink);
    font-weight: 900;
    font-size: 20px;
    line-height: 22px;
    white-space: nowrap;
  }

  .warning {
    padding: 36px 26px 0;
    text-align: center;
    color: var(--warning-ink);
    font-size: 10.4px;
    line-height: 16.6px;
    font-weight: 400;
  }
  .warning__title {
    display: block;
    font-weight: 700;
    font-size: 11.6px;
    color: var(--ink);
  }
  .facts {
    position: absolute;
    left: 12px;
    right: 12px;
    bottom: 20px;
    display: flex;
    justify-content: space-between;
    font-size: 10px;
    font-weight: 700;
    color: var(--ink);
  }

  .label__bottom {
    flex: 1;
    border-top: 2px solid var(--gold);
    margin-top: 3px;
    display: flex;
    flex-direction: column;
    align-items: center;
    padding-top: 12px;
  }
  .origin {
    font-family: "Cormorant Garamond", serif;
    font-weight: 700;
    color: var(--gold);
    font-size: 20px;
    letter-spacing: 3px;
    padding: 0 2px 2px;
    border-bottom: 1px solid var(--gold);
  }
  .vintage {
    margin-top: 6px;
    color: var(--year);
    font-family: "Cinzel", serif;
    font-size: 11px;
    letter-spacing: 8px;
    padding-left: 8px;
  }
</style>
</head>
<body>

  <section class="label label--front">
    <header class="label__top">
      <h1 class="varietal">SYMPHONY</h1>
    </header>
    <div class="label__panel" role="img" aria-label="Cream label panel with a soft damask pattern">
      <div class="brand-mark"></div>
      <p class="producer">MARK<br>DUNLOW</p>
    </div>
    <footer class="label__bottom">
      <p class="origin">Lodi, California</p>
      <p class="vintage">2016</p>
    </footer>
  </section>

  <section class="label label--back">
    <header class="label__top">
      <p class="website">WWW.DUNLOWVINCO.COM</p>
    </header>
    <div class="label__panel" role="img" aria-label="Cream label panel with a soft damask pattern">
      <p class="warning">
        <span class="warning__title">GOVERNMENT WARNING:</span>
        (1) ACCORDING TO THE SURGEON GENERAL, WOMEN SHOULD NOT DRINK ALCOHOLIC BEVERAGES DURING PREGNANCY BECAUSE OF THE RISK OF BIRTH DEFECTS.<br>
        (2) CONSUMPTION OF ALCOHOLIC BEVERAGES IMPAIRS YOUR ABILITY TO DRIVE A CAR OR OPERATE MACHINERY, AND MAY CAUSE HEALTH PROBLEMS.
      </p>
      <div class="facts">
        <span>CONTAINS SULFITES</span>
        <span>ALC 14.2% BY VOL</span>
        <span>750ML</span>
      </div>
    </div>
    <footer class="label__bottom">
      <p class="origin">Lodi, California</p>
      <p class="vintage">2016</p>
    </footer>
  </section>

</body>
</html>
```